Harborlight Amusement Collective (HAC)

We need a business card design for Harborlight Amusement Collective. Modern and sleek looking, with all critical information. Open to single or double sided designs, if double sided info needs to be all on one side. The main Logo is Harborlight Amusement collective and must be on the card. The other three logos are for the brands that fall under the group, they might be good on the back.

Industry/Entity Type

Business

```html
<!DOCTYPE html>
<html lang="en">
<head>
<meta charset="utf-8">
<title>Harborlight Amusement Collective – Business Card</title>
<link href="https://fonts.googleapis.com/css2?family=Montserrat:wght@400;500;600;700;800&family=Fira+Sans+Condensed:wght@600&display=swap" rel="stylesheet">
<style>
  :root {
    --bg: #d6d6d6;
    --card: #ffffff;
    --blue: #2a5ba4;
    --green: #8aa53a;
    --ink: #2b2b2b;
    --muted: #555555;
    --rule: #c9c9c9;
  }
  * { box-sizing: border-box; margin: 0; padding: 0; }
  html, body { width: 1200px; height: 852px; overflow: hidden; }
  body {
    background: var(--bg);
    font-family: "Montserrat", Arial, sans-serif;
    color: var(--ink);
    position: relative;
  }
  .card {
    position: absolute;
    width: 525px;
    height: 300px;
    background: var(--card);
    border-radius: 22px;
    box-shadow: 0 6px 18px rgba(0,0,0,.18);
  }
  /* Front */
  .card-front { left: 50px; top: 120px; text-align: center; padding-top: 30px; }
  .wordmark { display: flex; align-items: center; justify-content: center; gap: 14px; }
  .wordmark-square { width: 46px; height: 46px; background: var(--blue); }
  .wordmark-name {
    color: var(--blue); font-weight: 800; font-size: 21px; line-height: 1.1;
    text-transform: uppercase; letter-spacing: .5px; text-align: left;
  }
  .rule-pair { display: flex; justify-content: center; gap: 150px; margin-top: 14px; }
  .rule-pair span { display: block; width: 110px; height: 2px; background: var(--blue); }
  .brands-label { margin-top: 6px; font-size: 12px; color: var(--muted); }
  .rule-long { width: 400px; height: 1px; background: var(--green); margin: 10px auto 0; }
  .brand-row { display: flex; justify-content: center; align-items: center; margin-top: 16px; }
  .brand { display: flex; align-items: center; gap: 7px; padding: 0 16px; font-size: 16px; font-weight: 700; }
  .brand + .brand { border-left: 1px solid var(--rule); }
  .brand-dot { width: 14px; height: 14px; border-radius: 50%; }
  .brand-tickets { color: var(--green); }
  .brand-tickets .brand-dot { background: var(--green); }
  .brand-boxseat { color: var(--ink); }
  .brand-boxseat .brand-dot { background: var(--ink); }
  .brand-gatepass { color: var(--blue); }
  .brand-gatepass .brand-dot { background: var(--blue); }
  .rule-green { width: 440px; height: 2px; background: var(--green); margin: 20px auto 0; }
  .site { margin-top: 12px; font-size: 13px; color: var(--ink); }
  .site b { color: var(--blue); font-weight: 500; }
  /* Back */
  .card-back { left: 625px; top: 432px; display: flex; align-items: center; padding: 0 30px 0 34px; gap: 28px; }
  .mark-block { width: 210px; display: flex; flex-direction: column; align-items: center; gap: 14px; }
  .mark-square { width: 130px; height: 130px; background: var(--blue); }
  .mark-name { color: var(--blue); font-weight: 700; font-size: 15px; text-align: center; line-height: 1.25; }
  .contact { font-size: 12.5px; line-height: 1.35; color: var(--ink); }
  .contact-name { font-family: "Fira Sans Condensed", Arial, sans-serif; font-weight: 600; font-size: 21px; color: var(--blue); line-height: 1.1; }
  .contact-title { margin-bottom: 16px; }
  .contact-address { margin-bottom: 8px; }
  .contact-line { display: flex; align-items: center; gap: 9px; }
  .contact-line svg { width: 12px; height: 12px; fill: var(--blue); flex: none; }
  .contact-line b { color: var(--blue); font-weight: 400; }
</style>
</head>
<body>
  <section class="card card-front" aria-label="Card front">
    <div class="wordmark">
      <span class="wordmark-square"></span>
      <span class="wordmark-name">Harborlight<br>Amusement Collective</span>
    </div>
    <div class="rule-pair"><span></span><span></span></div>
    <p class="brands-label">Our Brands</p>
    <div class="rule-long"></div>
    <div class="brand-row">
      <div class="brand brand-tickets"><span class="brand-dot"></span>HarborTickets</div>
      <div class="brand brand-boxseat"><span class="brand-dot"></span>Boxseat Hospitality</div>
      <div class="brand brand-gatepass"><span class="brand-dot"></span>gatepass</div>
    </div>
    <div class="rule-green"></div>
    <p class="site">www.<b>harborlightcollective</b>.com</p>
  </section>

  <section class="card card-back" aria-label="Card back">
    <div class="mark-block">
      <span class="mark-square"></span>
      <span class="mark-name">Harborlight Amusement Collective</span>
    </div>
    <div class="contact">
      <p class="contact-name">Jordan Reyes Hale</p>
      <p class="contact-title">Managing Director</p>
      <p class="contact-address">118 Quayside Ave., Port<br>Town, US 482910</p>
      <p class="contact-line">
        <svg viewBox="0 0 24 24"><path d="M6.6 10.8a15 15 0 0 0 6.6 6.6l2.2-2.2c.3-.3.7-.4 1-.2 1.1.4 2.3.6 3.6.6.6 0 1 .4 1 1V20c0 .6-.4 1-1 1A17 17 0 0 1 3 4c0-.6.4-1 1-1h3.5c.6 0 1 .4 1 1 0 1.3.2 2.5.6 3.6.1.3 0 .7-.2 1z"/></svg>
        555.284.7193
      </p>
      <p class="contact-line">
        <svg viewBox="0 0 24 24"><path d="M2 5h20v14H2zm2 2v.5l8 5 8-5V7zm0 3v7h16v-7l-8 5z"/></svg>
        jhale@harborlightac.com
      </p>
      <p class="contact-line">
        <svg viewBox="0 0 24 24"><path d="M12 2a10 10 0 1 0 0 20 10 10 0 0 0 0-20zm6.9 6h-3a15 15 0 0 0-1.3-3.9A8 8 0 0 1 18.9 8zM12 4c.8 1.2 1.5 2.5 1.9 4h-3.8c.4-1.5 1.1-2.8 1.9-4zM4.3 14a8 8 0 0 1 0-4h3.4a16 16 0 0 0 0 4zm.8 2h3a15 15 0 0 0 1.3 3.9A8 8 0 0 1 5.1 16zm3-8h-3a8 8 0 0 1 4.3-3.9C8.8 5.3 8.4 6.6 8.1 8zM12 20c-.8-1.2-1.5-2.5-1.9-4h3.8c-.4 1.5-1.1 2.8-1.9 4zm2.3-6H9.7a14 14 0 0 1 0-4h4.6a14 14 0 0 1 0 4zm.3 5.9c.6-1.2 1-2.5 1.3-3.9h3a8 8 0 0 1-4.3 3.9zm1.7-5.9a16 16 0 0 0 0-4h3.4a8 8 0 0 1 0 4z"/></svg>
        www.<b>harborlightac</b>.com
      </p>
    </div>
  </section>
</body>
</html>
```